Marble Orchard - Report on digital habits and attitudes

We are a research company and we have written a PowerPoint Report to present the results of a series of surveys conducted in the last three years. The research is about the "Marble Orchard": people are facing the opportunities and challanges of their lives transformed by the digital technologies. We have investigated a number of topics through thousands of interviews and we've analyzed the data presented in the PowerPoint document.
We're not quite satisfied with the look and feel of the report: it looks too flat and boring, too "basic" to be presented as a professional work, yet being just that. We'd like you to upgrade the graphics and style of the report up to the level of a professional research product. The document still needs to be fully editable (either text and charts) but you can rearrange all the contents as you please, adding images, changing font and text size, colors and whatever you think is necessary to reach our goal.

Target Market(s)

Media covering digital issues
Marketing executives
Public institutions and policy makers

Industry/Entity Type

Market Research

Requirements
Must have
• The treats of a professional work
Fully editable within PowerPoint (either text and charts)
Nice to have
• Smart images
Original organization of the pages
Colors and graphics coherent with the quillbrook.it logo/website look and feel
Should not have
• PPT document over 30 MBytes
Images violating copyright

```html
<!DOCTYPE html>
<html lang="it">
<head>
<meta charset="utf-8">
<title>Marble Orchard – Le paure</title>
<link rel="stylesheet" href="https://fonts.googleapis.com/css2?family=Carlito:ital,wght@0,400;0,700;1,400;1,700&display=swap">
<style>
  :root {
    --ink: #1a1d24;
    --muted: #4a5263;
    --navy: #1f3864;
    --navy-deep: #14264a;
    --blue: #0070c0;
    --label: #3d4b63;
    --grid: #e3e7ee;
    --frame: #c9d1dd;
    --card: #fbfcfe;
    --accent-top: #8fa83a;
    --accent-bottom: #d6dcb0;
    --orange: #e07b1f;
    --point-dark: #14264a;
    --point-grey: #a6adb8;
    --paper: #ffffff;
  }
  * { margin: 0; padding: 0; box-sizing: border-box; }
  html, body { width: 760px; height: 1200px; overflow: hidden; background: var(--paper); }
  body { font-family: "Carlito", "Calibri", sans-serif; color: var(--ink); }
  .page { position: relative; width: 760px; height: 1200px; }

  .header-rule {
    position: absolute; left: 49px; top: 78px; width: 662px; height: 1px;
    background: linear-gradient(to right, var(--accent-top), var(--frame) 40%, transparent);
  }
  .section-bar {
    position: absolute; left: 49px; top: 44px; width: 8px; height: 26px; border-radius: 1px;
    background: linear-gradient(to bottom, var(--accent-top), var(--accent-bottom));
  }
  .section-title {
    position: absolute; left: 77px; top: 41px; font-size: 20px; font-weight: 700;
    color: var(--navy-deep); letter-spacing: 0.2px;
  }
  .page-number {
    position: absolute; left: 688px; top: 48px; width: 20px; height: 20px; border-radius: 50%;
    background: var(--navy); color: #fff; font-size: 11px; font-weight: 700;
    display: flex; align-items: center; justify-content: center;
  }

  .copy { position: absolute; font-size: 11.2px; color: var(--ink); }
  .copy b { color: var(--navy); font-weight: 700; }
  .copy i { color: var(--navy); }
  .copy .ln { display: block; white-space: nowrap; }
  .copy.spaced .ln { height: 36.7px; line-height: 36.7px; }
  .copy.tight .ln { height: 35px; line-height: 35px; }
  .copy.justified .ln { text-align: justify; text-align-last: justify; white-space: normal; }
  .copy.justified .ln.last { text-align-last: left; }

  .charts { position: absolute; left: 0; top: 0; width: 760px; height: 1200px; }
  .chart-frame { fill: var(--card); stroke: var(--frame); stroke-width: 2; }
  .chart-title-pill { fill: var(--navy); }
  .chart-title { font-family: "Carlito", "Calibri", sans-serif; font-size: 23px; font-weight: 700; fill: #ffffff; text-anchor: middle; letter-spacing: 0.4px; }
  .grid { stroke: var(--grid); stroke-width: 1.6; }
  .axis { stroke: #b8c1cf; stroke-width: 2; }
  .axis-label { font-family: "Carlito", "Calibri", sans-serif; font-size: 21px; font-weight: 700; fill: var(--navy); text-anchor: middle; }
  .value { font-family: "Carlito", "Calibri", sans-serif; font-size: 23px; font-weight: 700; fill: var(--label); text-anchor: middle; }
  .trend { fill: none; stroke: var(--navy); stroke-width: 3; stroke-linecap: round; }
  .area { fill: url(#areaFade); }
  .pt { stroke: #ffffff; stroke-width: 3; }
  .pt-dark { fill: var(--point-dark); }
  .pt-grey { fill: var(--point-grey); }
  .pt-blue { fill: var(--blue); }

  .footer-rule { position: absolute; left: 49px; top: 1136px; width: 662px; height: 1px; background: var(--frame); }
  .footer { position: absolute; left: 48px; top: 1148px; display: flex; align-items: center; gap: 6px; font-size: 11.2px; color: var(--muted); }
  .footer-brand { color: var(--navy); font-weight: 700; }
  .footer-mark { width: 9px; height: 9px; border-radius: 50%; background: var(--orange); }
</style>
</head>
<body>
<div class="page">
  <div class="section-bar"></div>
  <h1 class="section-title">Le paure</h1>
  <div class="page-number">3</div>
  <div class="header-rule"></div>

  <div class="copy spaced justified" style="left:57px; top:91px; width:280px;">
    <span class="ln">Otto persone su dieci ritengono che nell’ambiente</span>
    <span class="ln">digitale si siano diffuse <b>pratiche di manipolazione</b> delle</span>
    <span class="ln">persone più efficaci rispetto al passato. Il riferimento al</span>
    <span class="ln">passato è relativo al ’900, epoca in cui i mezzi di</span>
    <span class="ln">comunicazione di massa, tutti broadcasting, erano</span>
    <span class="ln last">gestiti dai governi e dai grandi editori.</span>
  </div>

  <div class="copy tight" style="left:57px; top:565px;">
    <span class="ln">Il sospetto sulla facilità di manipolazione delle</span>
    <span class="ln">persone è molto stabile e non si rileva alcuna tendenza</span>
    <span class="ln">significativa in tutto il periodo considerato.</span>
  </div>

  <div class="copy spaced" style="left:55px; top:960px;">
    <span class="ln">Il timore che il digitale ostacoli i rapporti e la socialità dei</span>
    <span class="ln">ragazzi è calato durante il primo lockdown, quando</span>
    <span class="ln">alcune formule di relazione digitale hanno «stupito» per</span>
    <span class="ln">essere in grado di</span>
  </div>

  <div class="copy spaced" style="left:426px; top:88px;">
    <span class="ln">supplire alla mancanza di quelle fisiche ed è diminuita la</span>
    <span class="ln"><i>condanna</i> verso le relazioni a distanza.</span>
    <span class="ln">La rilevazione successiva, però, ha mostrato che il</span>
    <span class="ln">cambiamento di giudizio è stato temporaneo e non si</span>
    <span class="ln">può ritenere un trend di lungo periodo: a novembre</span>
    <span class="ln">2020 la <i>paura che</i> le <b>relazioni a distanza deteriorino la</b></span>
    <span class="ln"><b>socialità</b> dei ragazzi è nuovamente aumentata,</span>
    <span class="ln">tornando ai livelli pre Covid.</span>
  </div>

  <div class="copy spaced" style="left:422px; top:624px;">
    <span class="ln">3 rispondenti su 4 (ovvero 30 milioni di individui, metà</span>
    <span class="ln">della popolazione italiana) sono convinti che <b>alcune</b></span>
    <span class="ln"><b>organizzazioni sappiano tutto di noi</b>, anche quando non</span>
    <span class="ln">siamo online. Il dato era leggermente aumentato nella</span>
    <span class="ln">primavera del 2020 probabilmente come conseguenza</span>
    <span class="ln">del dibattito sulle capacità dei sistemi di tracciamento</span>
    <span class="ln">nel contrastare la diffusione del contagio ma è rientrato</span>
    <span class="ln">ai livelli pre Covid.</span>
  </div>

  <div class="copy spaced" style="left:422px; top:920px;">
    <span class="ln">Questo aspetto è stato incluso tra gli atteggiamenti di</span>
    <span class="ln">sospetto ma il giudizio negativo potrebbe riguardare</span>
    <span class="ln">solo una parte dei cittadini: altri – di cui tuttavia</span>
    <span class="ln">ignoriamo il numero – potrebbero ritenere che il</span>
    <span class="ln">controllo sociale sia un aspetto positivo del digitale.</span>
  </div>

  <svg class="charts" viewBox="0 0 760 1200" aria-label="Grafici delle paure digitali">
    <defs>
      <linearGradient id="areaFade" x1="0" y1="0" x2="0" y2="1">
        <stop offset="0" stop-color="#0070c0" stop-opacity="0.16"/>
        <stop offset="1" stop-color="#0070c0" stop-opacity="0"/>
      </linearGradient>
      <filter id="cardShadow" x="-5%" y="-5%" width="110%" height="115%">
        <feDropShadow dx="0" dy="4" stdDeviation="6" flood-color="#1f3864" flood-opacity="0.12"/>
      </filter>
    </defs>
    <g transform="scale(0.4967)">
      <g class="chart manipulation">
        <rect class="chart-frame" filter="url(#cardShadow)" x="95" y="678" width="605" height="424" rx="20"/>
        <rect class="chart-title-pill" x="215" y="662" width="364" height="32" rx="16"/>
        <text class="chart-title" x="397" y="686">La manipolazione delle persone</text>
        <g>
          <line class="grid" x1="126" y1="755" x2="668" y2="755"/>
          <line class="grid" x1="126" y1="800" x2="668" y2="800"/>
          <line class="grid" x1="126" y1="845" x2="668" y2="845"/>
          <line class="grid" x1="126" y1="890" x2="668" y2="890"/>
          <line class="grid" x1="126" y1="935" x2="668" y2="935"/>
          <line class="grid" x1="126" y1="980" x2="668" y2="980"/>
          <path class="axis" d="M126 1025 H668 M126 1025 v6 M234 1025 v6 M343 1025 v6 M451 1025 v6 M560 1025 v6 M668 1025 v6"/>
        </g>
        <text class="axis-label" x="180" y="1063">Feb 19</text>
        <text class="axis-label" x="288" y="1063">Ott 19</text>
        <text class="axis-label" x="397" y="1063">Feb 20</text>
        <text class="axis-label" x="505" y="1063">Mag 20</text>
        <text class="axis-label" x="614" y="1063">Nov 20</text>
        <path class="area" d="M177 813 C220 832 255 845 286 861 C330 885 360 925 388 915 C425 902 460 808 501 794 C540 778 575 773 615 773 V1025 H177 Z"/>
        <path class="trend" d="M177 813 C220 832 255 845 286 861 C330 885 360 925 388 915 C425 902 460 808 501 794 C540 778 575 773 615 773"/>
        <circle class="pt pt-dark" cx="177" cy="813" r="9"/>
        <circle class="pt pt-grey" cx="286" cy="861" r="9"/>
        <circle class="pt pt-blue" cx="388" cy="915" r="9"/>
        <circle class="pt pt-dark" cx="501" cy="794" r="9"/>
        <circle class="pt pt-blue" cx="615" cy="773" r="9"/>
        <text class="value" x="180" y="854">79%</text>
        <text class="value" x="289" y="904">78%</text>
        <text class="value" x="397" y="953">77%</text>
        <text class="value" x="506" y="832">79%</text>
        <text class="value" x="614" y="814">80%</text>
      </g>

      <g class="chart big-brother">
        <rect class="chart-frame" filter="url(#cardShadow)" x="841" y="822" width="586" height="385" rx="20"/>
        <rect class="chart-title-pill" x="1031" y="806" width="204" height="32" rx="16"/>
        <text class="chart-title" x="1133" y="830">Il <tspan font-style="italic">Grande Fratello</tspan></text>
        <g>
          <line class="grid" x1="862" y1="856" x2="1405" y2="856"/>
          <line class="grid" x1="862" y1="888" x2="1405" y2="888"/>
          <line class="grid" x1="862" y1="920" x2="1405" y2="920"/>
          <line class="grid" x1="862" y1="952" x2="1405" y2="952"/>
          <line class="grid" x1="862" y1="984" x2="1405" y2="984"/>
          <line class="grid" x1="862" y1="1016" x2="1405" y2="1016"/>
          <line class="grid" x1="862" y1="1048" x2="1405" y2="1048"/>
          <line class="grid" x1="862" y1="1080" x2="1405" y2="1080"/>
          <line class="grid" x1="862" y1="1112" x2="1405" y2="1112"/>
          <path class="axis" d="M862 1145 H1405 M862 1145 v6 M971 1145 v6 M1079 1145 v6 M1188 1145 v6 M1296 1145 v6 M1405 1145 v6"/>
        </g>
        <text class="axis-label" x="917" y="1183">Feb 19</text>
        <text class="axis-label" x="1025" y="1183">Ott 19</text>
        <text class="axis-label" x="1134" y="1183">Feb 20</text>
        <text class="axis-label" x="1242" y="1183">Mag 20</text>
        <text class="axis-label" x="1351" y="1183">Nov 20</text>
        <path class="area" d="M917 1034 C955 1010 985 986 1017 976 C1055 965 1095 995 1125 991 C1165 985 1200 880 1241 877 C1290 873 1315 935 1351 942 V1145 H917 Z"/>
        <path class="trend" d="M917 1034 C955 1010 985 986 1017 976 C1055 965 1095 995 1125 991 C1165 985 1200 880 1241 877 C1290 873 1315 935 1351 942"/>
        <circle class="pt pt-dark" cx="917" cy="1034" r="9"/>
        <circle class="pt pt-grey" cx="1017" cy="976" r="9"/>
        <circle class="pt pt-blue" cx="1125" cy="991" r="9"/>
        <circle class="pt pt-dark" cx="1241" cy="877" r="9"/>
        <circle class="pt pt-blue" cx="1351" cy="942" r="9"/>
        <text class="value" x="917" y="1077">72%</text>
        <text class="value" x="1025" y="1016">74%</text>
        <text class="value" x="1134" y="1029">74%</text>
        <text class="value" x="1242" y="917">77%</text>
        <text class="value" x="1351" y="984">75%</text>
      </g>

      <g class="chart sociality">
        <rect class="chart-frame" filter="url(#cardShadow)" x="95" y="1441" width="601" height="424" rx="20"/>
        <rect class="chart-title-pill" x="233" y="1425" width="310" height="32" rx="16"/>
        <text class="chart-title" x="388" y="1449">Socialità e rapporti umani</text>
        <g>
          <line class="grid" x1="131" y1="1482" x2="664" y2="1482"/>
          <line class="grid" x1="131" y1="1517" x2="664" y2="1517"/>
          <line class="grid" x1="131" y1="1552" x2="664" y2="1552"/>
          <line class="grid" x1="131" y1="1587" x2="664" y2="1587"/>
          <line class="grid" x1="131" y1="1622" x2="664" y2="1622"/>
          <line class="grid" x1="131" y1="1657" x2="664" y2="1657"/>
          <line class="grid" x1="131" y1="1692" x2="664" y2="1692"/>
          <line class="grid" x1="131" y1="1727" x2="664" y2="1727"/>
          <line class="grid" x1="131" y1="1762" x2="664" y2="1762"/>
          <path class="axis" d="M131 1800 H664 M131 1800 v6 M238 1800 v6 M344 1800 v6 M451 1800 v6 M557 1800 v6 M664 1800 v6"/>
        </g>
        <text class="axis-label" x="184" y="1837">Feb 19</text>
        <text class="axis-label" x="291" y="1837">Ott 19</text>
        <text class="axis-label" x="397" y="1837">Feb 20</text>
        <text class="axis-label" x="504" y="1837">Mag 20</text>
        <text class="axis-label" x="611" y="1837">Nov 20</text>
        <path class="area" d="M185 1516 C225 1540 255 1582 286 1576 C330 1568 355 1508 391 1518 C440 1532 460 1700 502 1692 C545 1684 580 1580 608 1528 V1800 H185 Z"/>
        <path class="trend" d="M185 1516 C225 1540 255 1582 286 1576 C330 1568 355 1508 391 1518 C440 1532 460 1700 502 1692 C545 1684 580 1580 608 1528"/>
        <circle class="pt pt-dark" cx="185" cy="1516" r="9"/>
        <circle class="pt pt-grey" cx="286" cy="1576" r="9"/>
        <circle class="pt pt-blue" cx="391" cy="1518" r="9"/>
        <circle class="pt pt-dark" cx="502" cy="1692" r="9"/>
        <circle class="pt pt-blue" cx="608" cy="1528" r="9"/>
        <text class="value" x="184" y="1555">77%</text>
        <text class="value" x="291" y="1618">75%</text>
        <text class="value" x="398" y="1561">77%</text>
        <text class="value" x="504" y="1734">72%</text>
        <text class="value" x="611" y="1505">77%</text>
      </g>
    </g>
  </svg>

  <div class="footer-rule"></div>
  <footer class="footer">
    <span class="footer-mark"></span>
    <span>|<span class="footer-brand">Marble Orchard</span> |&nbsp; dicembre 2020 |&nbsp; © Quillbrook 2020</span>
  </footer>
</div>
</body>
</html>
```